Private Investment Firm Needs PowerPoint Presentation Template

Design PowerPoint template, take Pinebrook-submitted rough presentation draft, and drop it into new template. See attached Project Brief file for more detail.
Updates

Some decent designs have been submitted but they seem to lack the understanding of our target markets. I am hopeful that more time and feedback will result in better results.

Target Market(s)

Private company owners and intermediaries.

Font styles to use
Serif

Colors
3176b5

Requirements
Must have
• See attached Project Brief.
Nice to have
Should not have
• No B2C fluff--this is a B2B project.

```html
<!DOCTYPE html>
<html lang="en">
<head>
<meta charset="utf-8">
<title>Pinebrook Capital – Presentation Template</title>
<link href="https://fonts.googleapis.com/css2?family=Raleway:wght@400;500;600;700;800&display=swap" rel="stylesheet">
<style>
:root{
  --navy:#27486a;
  --blue:#1a6fbb;
  --accent:#3176b5;
  --teal:#1a9a86;
  --row:#d9d9d9;
  --shaft:#6b6b6b;
  --section-bg:#f1f1f1;
  --ink:#111;
  --body:#555;
  --sub:#777;
}
*{box-sizing:border-box;margin:0;padding:0}
html,body{width:1200px;height:1200px;overflow:hidden;background:#e6e6e6}
body{position:relative;font-family:'Raleway',sans-serif}
.slide{position:absolute;width:398px;height:398px;overflow:hidden;background:#fff}
.slide.section{background:var(--section-bg)}
.c1{left:0}.c2{left:402px}.c3{left:804px}
.r1{top:0}.r2{top:402px}.r3{top:804px}

.top-band{position:absolute;top:0;left:38px;width:360px;height:22px}
.top-band .accent{position:absolute;left:0;top:0;width:40px;height:16px;background:var(--accent);clip-path:polygon(0 0,60% 0,100% 100%,40% 100%)}
.top-band .bar{position:absolute;left:18px;top:0;right:0;height:22px;background:var(--navy);clip-path:polygon(0 0,100% 0,100% 100%,8% 100%)}

.bottom-band{position:absolute;left:0;bottom:0;width:300px;height:24px}
.bottom-band .bar{position:absolute;left:0;top:0;width:272px;height:24px;background:var(--navy);clip-path:polygon(0 0,92% 0,100% 100%,0 100%)}
.bottom-band .accent{position:absolute;left:262px;top:6px;width:36px;height:18px;background:var(--accent);clip-path:polygon(0 0,45% 0,100% 100%,55% 100%)}
.page-no{position:absolute;left:0;width:272px;top:5px;text-align:center;color:#fff;font-size:11px;font-weight:700}

.brand{position:absolute;right:12px;bottom:6px;display:flex;align-items:center;gap:4px}
.brand .dot{width:14px;height:14px;border-radius:50%;background:var(--accent)}
.brand .name{font-size:10.5px;font-weight:600;color:var(--navy);letter-spacing:.6px}

.title{position:absolute;left:0;right:0;text-align:center;color:var(--blue);font-weight:800;line-height:1.1}
.section .title{top:180px;font-size:27px}

.bullets{position:absolute;list-style:none}
.bullets li{position:relative;padding-left:13px;color:var(--body);font-weight:600}
.bullets li::before{content:"";position:absolute;left:1px;top:.45em;width:5px;height:5px;border-radius:50%;background:var(--accent)}
.bullets .sub{padding-left:18px;font-weight:500;color:var(--sub);font-size:9px}
.bullets .sub::before{content:"-";background:none;width:auto;height:auto;top:0;left:12px;color:var(--sub)}
.hl{color:var(--blue)}

/* balance sheet */
.sheet{position:absolute;left:18px;top:126px;width:364px}
.sheet .row{display:flex;height:20px;margin-bottom:0}
.sheet .cell{flex:0 0 160px;background:var(--row);font-size:11px;font-weight:700;color:var(--ink);padding:3px 0 0 20px;border-bottom:2px solid #fff}
.sheet .shaft{flex:0 0 28px;background:var(--shaft);border-bottom:2px solid var(--shaft)}
.sheet .cell.r{flex:1;padding-left:20px}
.sheet .teal{background:var(--teal);color:#fff}
.sheet .blue{background:var(--blue);color:#fff}
.sheet .blank{background:var(--row)}
.key{position:absolute;top:352px;left:0;right:0;text-align:center;font-size:9px;font-weight:700;color:var(--ink)}

/* case study cards */
.card{position:absolute;left:37px;width:324px;display:flex;border:1.5px solid var(--teal);background:#fff}
.card .label{flex:0 0 124px;text-align:center;padding-top:14px}
.card .label h4{font-size:11.5px;font-weight:700;color:var(--blue);line-height:1.2}
.card .company{margin-top:22px;display:flex;align-items:center;justify-content:center;gap:5px}
.card .company .sq{width:12px;height:12px;background:var(--navy)}
.card .company span{font-size:10.5px;font-weight:700;color:var(--navy)}
.card .detail{flex:1;background:var(--teal);color:#fff;font-size:6.6px;line-height:1.3;padding:8px 6px 4px 8px;list-style:none}
.card .detail li{position:relative;padding-left:8px;margin-bottom:7px}
.card .detail li::before{content:"";position:absolute;left:0;top:2px;width:3px;height:3px;border-radius:50%;background:#fff}
</style>
</head>
<body>

<!-- Slide 9 -->
<section class="slide c1 r1">
  <div class="top-band"><div class="accent"></div><div class="bar"></div></div>
  <h2 class="title" style="top:46px;font-size:22.5px">A Balance Sheet: Pinebrook's<br>Position In The Capital Stack</h2>
  <div class="sheet">
    <div class="row"><div class="cell teal">Assets</div><div class="shaft"></div><div class="cell r teal">Liabilities</div></div>
    <div class="row"><div class="cell">Cash</div><div class="shaft"></div><div class="cell r">Accounts Payable</div></div>
    <div class="row"><div class="cell">Marketable Securities</div><div class="shaft"></div><div class="cell r">Taxes Payable</div></div>
    <div class="row"><div class="cell">Accounts Receivable</div><div class="shaft"></div><div class="cell r">Revolver</div></div>
    <div class="row"><div class="cell">Inventory</div><div class="shaft"></div><div class="cell r">Senior Term Loan</div></div>
    <div class="row"><div class="cell">PP&amp;E</div><div class="shaft"></div><div class="cell r">Unitranche Debt</div></div>
    <div class="row"><div class="cell teal">Intangible Assets</div><div class="shaft"></div><div class="cell r teal">Subordinated Debt*</div></div>
    <div class="row"><div class="cell blue">Other Assets</div><div class="shaft"></div><div class="cell r blue">Equity</div></div>
    <div class="row"><div class="cell blank"></div><div class="shaft"></div><div class="cell r">Owners' Equity</div></div>
    <div class="row"><div class="cell teal"></div><div class="shaft"></div><div class="cell r teal">Preferred Stock</div></div>
    <div class="row"><div class="cell teal"></div><div class="shaft"></div><div class="cell r teal">Common Stock</div></div>
  </div>
  <p class="key">*Key: Where Pinebrook Participates</p>
  <div class="bottom-band"><div class="bar"></div><div class="accent"></div><span class="page-no">9</span></div>
  <div class="brand"><span class="dot"></span><span class="name">PINEBROOK</span></div>
</section>

<!-- Section -->
<section class="slide section c2 r1">
  <h2 class="title">Firm Overview</h2>
</section>

<!-- Slide 10 -->
<section class="slide c3 r1">
  <div class="top-band"><div class="accent"></div><div class="bar"></div></div>
  <h2 class="title" style="top:58px;font-size:25px">Pinebrook Capital Introduction</h2>
  <ul class="bullets" style="left:14px;top:110px;width:384px;font-size:11.5px;line-height:1.2">
    <li>Pinebrook invests Non-Control Capital direct with management</li>
    <li class="sub" style="margin-top:6px">Owners retain control of their business after we invest</li>
    <li class="sub" style="margin-top:8px">Without a traditional Change-of-Control private equity sponsor</li>
    <li style="margin-top:18px">One of the longest-standing junior capital funds targeting the lower middle market</li>
    <li style="margin-top:14px">Since 1994, Pinebrook has completed 74 (and counting) Non-Control Capital investments and managed over $600 million</li>
    <li style="margin-top:14px">Our interests are aligned with management or we don't invest</li>
    <li style="margin-top:14px">"Consultants with Capital"</li>
    <li class="sub" style="margin-top:6px;line-height:1.9">We partner with companies that seek capital and our assistance to improve and/or grow the business</li>
  </ul>
  <div class="bottom-band"><div class="bar"></div><div class="accent"></div><span class="page-no">10</span></div>
  <div class="brand"><span class="dot"></span><span class="name">PINEBROOK</span></div>
</section>

<!-- Section -->
<section class="slide section c1 r2">
  <h2 class="title">Firm Overview</h2>
</section>

<!-- Slide 11 -->
<section class="slide c2 r2">
  <div class="top-band"><div class="accent"></div><div class="bar"></div></div>
  <h2 class="title" style="top:62px;font-size:21px">We Have Over 140 Years Of Combined<br>Principal Investing Experience.</h2>
  <ul class="bullets" style="left:12px;top:126px;width:380px;font-size:11.5px;line-height:1.2">
    <li>Offices in Boston and San Francisco with 12 investment professionals <span class="hl">fully dedicated</span> to Non-Control Capital investing</li>
    <li style="margin-top:14px">Invest combinations of equity and subordinated debt securities</li>
    <li style="margin-top:14px">Currently investing $260MM fourth fund</li>
    <li class="sub" style="margin-top:6px">9 Fund IV investments made to date (as of November 1, 2018)</li>
    <li class="sub" style="margin-top:8px">Over $120MM of "dry powder" available for new investments</li>
  </ul>
  <div class="bottom-band"><div class="bar"></div><div class="accent"></div><span class="page-no">11</span></div>
  <div class="brand"><span class="dot"></span><span class="name">PINEBROOK</span></div>
</section>

<!-- Section -->
<section class="slide section c3 r2">
  <h2 class="title">What We Do / And Why</h2>
</section>

<!-- Slide 12 -->
<section class="slide c1 r3">
  <div class="top-band"><div class="accent"></div><div class="bar"></div></div>
  <h2 class="title" style="top:60px;font-size:23px">Non-Control Capital<br>Transactions Only</h2>
  <ul class="bullets" style="left:14px;top:130px;width:375px;font-size:11.5px;line-height:1.2">
    <li>Companies looking for a partner to help them grow, not sellers looking to exit</li>
    <li style="margin-top:10px">Management's personal wealth directly tied to the performance of the investment</li>
    <li style="margin-top:14px">Situational investors with a generalist approach</li>
    <li style="margin-top:16px">Our heritage reflects decades of Non-Control Capital investing—it's all we do</li>
  </ul>
  <div class="bottom-band"><div class="bar"></div><div class="accent"></div><span class="page-no">12</span></div>
  <div class="brand"><span class="dot"></span><span class="name">PINEBROOK</span></div>
</section>

<!-- Slide 13 -->
<section class="slide c2 r3">
  <div class="top-band"><div class="accent"></div><div class="bar"></div></div>
  <h2 class="title" style="top:60px;font-size:23px">Pinebrook Representative<br>Non-Control Capital Investments</h2>
  <div class="card" style="top:132px;height:112px">
    <div class="label"><h4>Growth Capital</h4><div class="company"><span class="sq"></span><span>Skyward Flight</span></div></div>
    <ul class="detail">
      <li>Runs dedicated commercial airline pilot training centers across the U.S. and Mexico. Sites include classrooms, integrated procedure trainers, flight training devices and Level D full-motion flight simulators.</li>
      <li>Pinebrook's capital was used to fund the Company's near to intermediate-term growth. Pinebrook also helped the Company recruit additional management staff and open a new Dallas office.</li>
    </ul>
  </div>
  <div class="card" style="top:248px;height:110px">
    <div class="label"><h4>Management<br>Buy-Out (MBO)</h4><div class="company" style="margin-top:14px"><span class="sq"></span><span>Marlow Consulting</span></div></div>
    <ul class="detail">
      <li>Provider of audit compliance software and consulting services for hospitals and physician practices.</li>
      <li>Pinebrook's capital was used to help the active CEO buy the business from its inactive founder. Pinebrook also helped fund major investment in the Company's core revenue integrity software, building it into the leading risk-based product in its sector.</li>
    </ul>
  </div>
  <div class="bottom-band"><div class="bar"></div><div class="accent"></div><span class="page-no">13</span></div>
  <div class="brand"><span class="dot"></span><span class="name">PINEBROOK</span></div>
</section>

<!-- Slide 14 -->
<section class="slide c3 r3">
  <div class="top-band"><div class="accent"></div><div class="bar"></div></div>
  <h2 class="title" style="top:60px;font-size:23px">Pinebrook Representative<br>Non-Control Capital Investments</h2>
  <div class="card" style="top:132px;height:112px">
    <div class="label"><h4>Acquisition Finance</h4><div class="company"><span class="sq"></span><span>Northline Group</span></div></div>
    <ul class="detail">
      <li>Maker of vibration isolation, seismic control and shock protection products. The Company's products are designed to limit vibration, impact, seismic and wind forces to protect larger systems at risk of damage.</li>
      <li>Pinebrook's capital was used to acquire two attractive tuck-in companies (a testing lab and an online parts distributor) that improved the Company's position. Three years later, it set an all-time sales record.</li>
    </ul>
  </div>
  <div class="card" style="top:248px;height:110px">
    <div class="label"><h4>Balance Sheet<br>Recapitalization</h4><div class="company" style="margin-top:14px"><span class="sq"></span><span>Fleetwise</span></div></div>
    <ul class="detail">
      <li>Provider of third-party vehicle maintenance services for private, public and for-hire fleet-based businesses nationwide.</li>
      <li>Pinebrook's capital was used to support the Company's fast growth, which exceeded its current lender's capacity. Pinebrook provided both subordinated debt and preferred stock, changed the debt and equity mix of the business, and the Company grew sharply over the next three years.</li>
    </ul>
  </div>
  <div class="bottom-band"><div class="bar"></div><div class="accent"></div><span class="page-no">14</span></div>
  <div class="brand"><span class="dot"></span><span class="name">PINEBROOK</span></div>
</section>

</body>
</html>
```